New Company Business Card design

Looking for a corporate looking business card utilising my new logo design - the logo i would like embossed as one option and flat as another - simplistic but stylish - less is more - we are an import export business launching into the market - i would like a couple of options as main background - Grey or Black

```html
<!DOCTYPE html>
<html lang="en">
<head>
<meta charset="utf-8">
<title>Corvane Trade Partners – Business Card</title>
<link rel="stylesheet" href="https://fonts.googleapis.com/css2?family=Cinzel:wght@500&family=Arimo:wght@400&display=swap">
<style>
  :root {
    --backdrop: #1a1a1c;
    --card: #141416;
    --card-edge: #2a2a2d;
    --brand-blue: #1f7fd1;
    --text-light: #e6e6e6;
    --text-muted: #9a9a9e;
    --rule: #3a3a3e;
  }
  * { margin: 0; padding: 0; box-sizing: border-box; }
  html, body {
    width: 1200px; height: 900px; overflow: hidden;
    background: var(--backdrop);
  }
  .canvas {
    position: relative; width: 1200px; height: 900px;
    display: flex; flex-direction: column; align-items: center; justify-content: center; gap: 50px;
  }
  .card {
    position: relative; width: 560px; height: 320px;
    background: var(--card);
    border-radius: 22px;
    border: 1px solid var(--card-edge);
    box-shadow: 0 18px 40px rgba(0,0,0,0.55);
  }
  .wordmark {
    font-family: "Cinzel", serif; font-weight: 500;
    color: var(--brand-blue); letter-spacing: 2px;
    display: flex; align-items: center; gap: 14px;
  }
  .wordmark .mark-dot {
    width: 22px; height: 22px; border-radius: 50%;
    background: var(--brand-blue); flex: none;
  }
  /* front */
  .card-front .wordmark {
    position: absolute; left: 0; right: 0; top: 105px;
    justify-content: center; font-size: 44px;
  }
  .card-front .website {
    position: absolute; left: 0; right: 0; top: 250px; text-align: center;
    font-family: "Arimo", sans-serif; font-size: 14px; letter-spacing: 1.5px;
    color: var(--text-muted);
  }
  .card-front .website span { color: var(--brand-blue); }
  /* back */
  .card-back .wordmark {
    position: absolute; right: 32px; top: 34px;
    font-size: 20px; line-height: 1.25; text-align: right;
  }
  .card-back .brand-rule {
    position: absolute; right: 32px; top: 118px; width: 250px; height: 1px;
    background: var(--rule);
  }
  .holder {
    position: absolute; left: 36px; top: 128px;
  }
  .holder-name {
    font-family: "Cinzel", serif; font-weight: 500; font-size: 18px;
    color: var(--brand-blue); letter-spacing: 1px;
  }
  .holder-role {
    font-family: "Arimo", sans-serif; font-size: 14px; color: var(--text-light);
    margin-top: 2px;
  }
  .address {
    position: absolute; right: 32px; top: 150px; text-align: right;
    font-family: "Arimo", sans-serif; font-size: 14px; line-height: 1.35;
    color: var(--text-light);
  }
  .card-back .divider {
    position: absolute; left: 36px; right: 32px; top: 212px; height: 1px;
    background: var(--rule);
  }
  .contacts {
    position: absolute; left: 36px; top: 232px; list-style: none;
    font-family: "Arimo", sans-serif; font-size: 15px; color: var(--text-light);
  }
  .contacts li { display: flex; align-items: center; gap: 10px; height: 21px; }
  .contacts svg { width: 13px; height: 13px; fill: var(--brand-blue); flex: none; }
</style>
</head>
<body>
<main class="canvas">
  <section class="card card-front" aria-label="Card front">
    <div class="wordmark"><span class="mark-dot"></span>Corvane</div>
    <p class="website">www.<span>corvanetrade</span>.com</p>
  </section>

  <section class="card card-back" aria-label="Card back">
    <div class="wordmark"><span class="mark-dot"></span><span>Corvane<br>Trade Partners</span></div>
    <div class="brand-rule"></div>

    <div class="holder">
      <p class="holder-name">ELIAS MARREN</p>
      <p class="holder-role">Managing Director</p>
    </div>

    <p class="address">48 Harbour Row, Dockside<br>Portland, 970412</p>

    <div class="divider"></div>

    <ul class="contacts">
      <li>
        <svg viewBox="0 0 16 16" aria-hidden="true"><path d="M3 1h3l1.5 4-2 1.3a9 9 0 0 0 4.2 4.2L11 8.5l4 1.5v3a2 2 0 0 1-2 2A13 13 0 0 1 1 3a2 2 0 0 1 2-2z"/></svg>
        044-555 201 730
      </li>
      <li>
        <svg viewBox="0 0 16 16" aria-hidden="true"><path d="M4 0h8a1 1 0 0 1 1 1v14a1 1 0 0 1-1 1H4a1 1 0 0 1-1-1V1a1 1 0 0 1 1-1zm1 2v10h6V2zm3 11a1 1 0 1 0 0 2 1 1 0 0 0 0-2z"/></svg>
        044-555 201 731
      </li>
      <li>
        <svg viewBox="0 0 16 16" aria-hidden="true"><path d="M1 3h14v10H1zm1.5 1.2V5l5.5 4 5.5-4v-.8z"/></svg>
        hello@corvanetrade.com
      </li>
    </ul>
  </section>
</main>
</body>
</html>
```